KPL Construction we build lodges in Botswana

We need a Design Layout only with Categories where we can update each projects photos.... We have a web address and a host - kpl.construction

```html
<!DOCTYPE html>
<html lang="en">
<head>
<meta charset="utf-8">
<title>KPL Construction – We build lodges in Botswana</title>
<link href="https://fonts.googleapis.com/css2?family=Roboto+Condensed:wght@400;700&family=Open+Sans:wght@400;600&display=swap" rel="stylesheet">
<style>
:root{
  --teal:#0f6e69;
  --teal-dark:#0b4a47;
  --teal-light:#bfe3e6;
  --orange:#e8542b;
  --ink:#2a2f33;
  --muted:#8a9096;
  --line:#e3e6e8;
  --footer:#15191c;
  --white:#ffffff;
}
*{box-sizing:border-box;margin:0;padding:0}
html,body{width:1200px;height:4836px;overflow:hidden}
body{position:relative;background:var(--white);font-family:"Open Sans",Arial,sans-serif;color:var(--ink)}
.abs{position:absolute}
.heading{font-family:"Roboto Condensed","Arial Narrow",sans-serif;font-weight:700;text-transform:uppercase;text-align:center;font-size:48px;color:var(--ink);left:0;width:1200px}
.heading-mark{width:44px;height:44px;background:var(--teal);left:578px}

/* header */
.site-header{top:0;left:0;width:1200px;height:180px;background:var(--white)}
.brand{left:90px;top:52px;display:flex;align-items:center;gap:18px}
.brand-mark{width:44px;height:44px;background:var(--teal)}
.brand-name{font-family:"Roboto Condensed",sans-serif;font-weight:700;font-size:40px;color:var(--teal);line-height:1}
.top-phone{left:700px;top:42px;font-size:22px;color:var(--ink);display:flex;align-items:center;gap:8px}
.search{left:904px;top:36px;width:206px;height:44px;border:2px solid var(--line);border-radius:22px;font-size:18px;color:var(--muted);padding:8px 18px}
.nav{left:480px;top:108px;display:flex;gap:44px;font-size:22px;font-weight:600}
.nav .active{color:var(--teal)}

/* hero */
.hero{top:180px;left:0;width:1200px;height:620px}
.hero-photo{position:absolute;inset:0;background:linear-gradient(160deg,#3b2a1e 0%,#6b4a2c 45%,#2b4450 70%,#1d2a30 100%)}
.hero-title{top:200px;left:0;width:1200px;text-align:center;color:var(--white);font-family:"Roboto Condensed",sans-serif;font-weight:700;font-size:72px}
.hero-sub{top:290px;left:0;width:1200px;text-align:center;color:var(--white);font-size:40px}

/* services */
.service{width:330px;text-align:center}
.service-icon{width:112px;height:112px;margin:0 auto;border-radius:50%;background:#fbe1d8;display:flex;align-items:center;justify-content:center}
.service h3{font-family:"Roboto Condensed",sans-serif;font-size:26px;margin-top:34px}
.service p{font-size:17px;line-height:26px;color:var(--muted);margin-top:18px}

/* about */
.about{top:1460px;left:0;width:1200px;height:640px;background:linear-gradient(180deg,#d6eef0,#a9d6da)}
.about-photo{left:120px;top:132px;width:460px;height:340px;background:linear-gradient(180deg,#8ec3e8 0%,#8a5a36 55%,#5f8a3c 100%)}
.about-frame{left:96px;top:106px;width:200px;height:200px;background:var(--orange)}
.about-text{left:612px;top:166px;width:490px}
.about-text h2{font-family:"Roboto Condensed",sans-serif;font-size:40px;font-weight:400}
.about-text h3{font-family:"Roboto Condensed",sans-serif;font-size:28px;font-weight:400;margin-top:4px}
.about-text p{font-size:15px;line-height:24px;color:#3b4a4e;margin-top:12px}
.btn{display:inline-block;background:var(--orange);color:var(--white);font-size:17px;padding:9px 24px;border-radius:6px;margin-top:18px}

/* projects */
.tile{position:absolute;width:332px;height:232px}
.view-more{left:980px;top:2896px;font-size:18px;color:var(--orange)}

/* testimonial */
.testimonial{top:3020px;left:0;width:1200px;height:540px;background:linear-gradient(180deg,#0d5f5b,#0a4a47)}
.testimonial .heading{color:var(--white);font-weight:400;top:140px;font-size:46px}
.quote{top:230px;left:130px;width:940px;text-align:center;color:#e6f1f0;font-size:17px;line-height:28px}
.avatar{left:548px;top:350px;width:104px;height:104px;border-radius:50%;background:#c9b8a6;border:4px solid var(--white)}
.person{top:472px;left:0;width:1200px;text-align:center;color:var(--white);font-size:18px}

/* blog */
.blog-photo{left:88px;top:3952px;width:452px;height:488px;background:linear-gradient(180deg,#e9a24a 0%,#c86a2b 55%,#3a2a1c 100%);box-shadow:0 4px 18px rgba(0,0,0,.18)}
.blog-card{left:532px;top:4000px;width:580px;height:392px;background:var(--white);box-shadow:0 4px 24px rgba(0,0,0,.14);padding:30px 36px}
.blog-card .date{font-size:15px;color:var(--orange)}
.blog-card h3{font-family:"Roboto Condensed",sans-serif;font-weight:400;font-size:34px;margin-top:8px}
.blog-card p{font-size:15px;line-height:24px;color:var(--muted);margin-top:14px}

/* footer */
.footer{top:4520px;left:0;width:1200px;height:316px;background:var(--footer)}
.social{display:flex;gap:14px;left:966px;top:36px}
.social span{width:26px;height:26px;background:#cfd3d6;display:block}
.newsletter-label{left:600px;top:128px;color:var(--white);font-size:20px;font-family:"Roboto Condensed",sans-serif}
.newsletter{left:818px;top:114px;width:292px;height:48px;border:2px solid #4a5358;border-radius:24px;color:#9aa1a6;font-size:17px;padding:11px 22px}
.footer-line{left:0;width:1200px;text-align:center;color:#c3c8cb;font-size:15px}
</style>
</head>
<body>

<header class="site-header abs">
  <div class="brand abs"><span class="brand-mark"></span><span class="brand-name">KPL Construction</span></div>
  <div class="top-phone abs">
    <svg width="20" height="20" viewBox="0 0 24 24"><path d="M6.6 10.8a15 15 0 0 0 6.6 6.6l2.2-2.2a1 1 0 0 1 1-.25 11.4 11.4 0 0 0 3.6.6 1 1 0 0 1 1 1V20a1 1 0 0 1-1 1A17 17 0 0 1 3 4a1 1 0 0 1 1-1h3.5a1 1 0 0 1 1 1c0 1.25.2 2.45.57 3.57a1 1 0 0 1-.25 1z" fill="#e8542b"/></svg>
    1-800-555-0142
  </div>
  <div class="search abs">Search</div>
  <nav class="nav abs"><span class="active">Home</span><span>About us</span><span>Services</span><span>Projects</span><span>Blog</span><span>Contact us</span></nav>
</header>

<section class="hero abs">
  <div class="hero-photo" role="img" aria-label="Evening view of a lodge deck with a round pool"></div>
  <div class="hero-title abs">KPL CONSTRUCTION</div>
  <div class="hero-sub abs">We build lodges in Botswana</div>
  <svg class="abs" style="left:0;top:0" width="1200" height="620">
    <polygon points="960,560 1200,480 1200,620 1000,620" fill="#e8542b"/>
    <polygon points="0,600 1200,520 1200,620 0,620" fill="#ffffff"/>
  </svg>
</section>

<div class="heading-mark abs" style="top:858px"></div>
<h2 class="heading abs" style="top:922px">Our Services</h2>

<div class="service abs" style="left:75px;top:1024px">
  <div class="service-icon"><svg width="60" height="60" viewBox="0 0 60 60" fill="none" stroke="#2a2f33" stroke-width="3"><path d="M12 12l36 36M48 12L12 48"/><circle cx="10" cy="10" r="6"/><circle cx="50" cy="50" r="6"/></svg></div>
  <h3>Project Development</h3>
  <p>The point of using Lorem Ipsum is that it has a more-or-less normal distribution of letters, as opposed</p>
  <svg width="20" height="20" viewBox="0 0 20 20" style="margin-top:12px"><path d="M3 4l7 6 7-6M3 11l7 6 7-6" stroke="#2a2f33" stroke-width="2.5" fill="none"/></svg>
</div>
<div class="service abs" style="left:435px;top:1024px">
  <div class="service-icon"><svg width="60" height="60" viewBox="0 0 60 60" fill="none" stroke="#2a2f33" stroke-width="3"><rect x="10" y="16" width="36" height="34"/><path d="M40 8l10 10-20 20H20V28z"/></svg></div>
  <h3>Drawing Services</h3>
  <p>The point of using Lorem Ipsum is that it has a more-or-less normal distribution of letters, as opposed</p>
  <svg width="20" height="20" viewBox="0 0 20 20" style="margin-top:12px"><path d="M3 4l7 6 7-6M3 11l7 6 7-6" stroke="#2a2f33" stroke-width="2.5" fill="none"/></svg>
</div>
<div class="service abs" style="left:795px;top:1024px">
  <div class="service-icon"><svg width="60" height="60" viewBox="0 0 60 60" fill="none" stroke="#2a2f33" stroke-width="3"><path d="M6 30L30 8l24 22M12 26v26h36V26"/><rect x="24" y="36" width="12" height="16"/></svg></div>
  <h3>Construction</h3>
  <p>The point of using Lorem Ipsum is that it has a more-or-less normal distribution of letters, as opposed</p>
  <svg width="20" height="20" viewBox="0 0 20 20" style="margin-top:12px"><path d="M3 4l7 6 7-6M3 11l7 6 7-6" stroke="#2a2f33" stroke-width="2.5" fill="none"/></svg>
</div>

<section class="about abs">
  <svg class="abs" style="left:0;top:0" width="1200" height="640">
    <polygon points="0,0 1200,0 1200,20 0,60" fill="#ffffff"/>
    <polygon points="0,500 520,640 0,640" fill="#0b4a47"/>
    <polygon points="0,640 1200,560 1200,640" fill="#ffffff"/>
  </svg>
  <div class="about-frame abs"></div>
  <div class="about-photo abs" role="img" aria-label="Thatched timber lodges on a green lawn"></div>
  <svg class="abs" style="left:318px;top:270px" width="64" height="64"><circle cx="32" cy="32" r="30" fill="rgba(0,0,0,.45)"/><polygon points="25,18 48,32 25,46" fill="#fff"/></svg>
  <div class="about-text abs">
    <h2>About</h2>
    <h3>KPL CONSTRUCTION</h3>
    <p>It is a long established fact that a reader will be distracted by the readable content of a page when looking at its layout. The point of using Lorem Ipsum is that it has a more-or-less normal distribution of letters, as opposed to using Content here, content here, making it look like readable English. Many desktop publishing packages and web page editors now use Lorem Ipsum as their default model text.</p>
    <span class="btn">Read More</span>
  </div>
</section>

<div class="heading-mark abs" style="top:2196px"></div>
<h2 class="heading abs" style="top:2262px">Our Projects</h2>

<div class="tile" style="left:88px;top:2380px;background:#d9522c;display:flex;align-items:center;justify-content:center;color:#fff;font-family:'Roboto Condensed',sans-serif;font-size:26px;text-align:center;text-transform:uppercase;line-height:34px">Neque porro<br>quisquam</div>
<div class="tile" role="img" aria-label="Lodge bedroom interior" style="left:432px;top:2380px;background:linear-gradient(160deg,#8a4a26,#c98a4e,#5a3220)"></div>
<div class="tile" role="img" aria-label="Wooden lodge among green trees" style="left:772px;top:2380px;background:linear-gradient(180deg,#cfe6f2,#6a8f3c 50%,#6a3b22)"></div>
<div class="tile" role="img" aria-label="Lodge terrace at dusk" style="left:88px;top:2628px;background:linear-gradient(180deg,#5d7f99,#34454f 55%,#8d7a62)"></div>
<div class="tile" role="img" aria-label="Yellow lodge with thatched roof" style="left:432px;top:2628px;background:linear-gradient(180deg,#a9d0ea,#d9b84a 55%,#7a8a3c)"></div>
<div class="tile" role="img" aria-label="Lodge suite with bed" style="left:772px;top:2628px;background:linear-gradient(160deg,#4a2e1e,#9a6a42,#2e1c12)"></div>
<div class="view-more abs">View More ▸</div>

<section class="testimonial abs">
  <svg class="abs" style="left:0;top:0" width="1200" height="540">
    <polygon points="0,0 1200,0 0,50" fill="#ffffff"/>
    <polygon points="0,540 1200,470 1200,540" fill="#ffffff"/>
  </svg>
  <h2 class="heading abs">Testimonial</h2>
  <p class="quote abs">“ It has survived not only five centuries, but also the leap into electronic typesetting, remaining essentially unchanged. It was popularised in the 1960s with the release of sheets containing Lorem Ipsum passages, and more recently with desktop publishing software including versions of Lorem Ipsum. ”</p>
  <svg class="abs" style="left:490px;top:388px" width="220" height="30"><path d="M16 4L6 15l10 11M204 4l10 11-10 11" stroke="#fff" stroke-width="3" fill="none"/></svg>
  <div class="avatar abs" role="img" aria-label="Client portrait"></div>
  <div class="person abs">Neque porro quisquam</div>
</section>

<div class="heading-mark abs" style="top:3776px"></div>
<h2 class="heading abs" style="top:3842px">Latest Blog</h2>

<div class="blog-photo abs" role="img" aria-label="Baobab trees at sunset"></div>
<article class="blog-card abs">
  <div class="date">05.07.2019</div>
  <h3>Neque porro quisquam est qui</h3>
  <p>It is a long established fact that a reader will be distracted by the readable content of a page when looking at its layout. The point of using Lorem Ipsum is that it has a more-or-less normal distribution of letters, as opposed to using Content here, making it look like readable English.</p>
  <span class="btn" style="font-size:15px;padding:7px 18px">Read More</span>
</article>
<svg class="abs" style="left:1060px;top:4438px" width="50" height="20"><path d="M12 3L5 10l7 7M38 3l7 7-7 7" stroke="#8a9096" stroke-width="2.5" fill="none"/></svg>

<footer class="footer abs">
  <svg class="abs" style="left:0;top:-60px" width="1200" height="120">
    <polygon points="0,0 1200,90 1200,120 0,120" fill="#15191c"/>
    <polygon points="0,0 640,48 0,70" fill="#0f6e69"/>
  </svg>
  <div class="social abs"><span></span><span></span><span></span><span></span></div>
  <div class="brand abs" style="top:116px;left:90px"><span class="brand-mark"></span><span class="brand-name">KPL Construction</span></div>
  <div class="newsletter-label abs">JOIN OUR NEWSLETTER</div>
  <div class="newsletter abs">Email address</div>
  <div class="footer-line abs" style="top:200px">6018 Acacia Ridge Road, Maun, Botswana 27105 &nbsp;|&nbsp; Ph: (267) 555-0142 &nbsp;|&nbsp; Email: info@kpl.construction</div>
  <div class="footer-line abs" style="top:246px">Copyright © 2019. All Rights Reserved</div>
</footer>

</body>
</html>
```